need a clean, modern job advertisement designed for social media (Facebook & Instagram).

The post is to advertise two positions:
• Leading Hand Boilermaker
• Dragline Fitter
We want the design to match our KPR Site Services branding: blue, white, strong, professional, mining-industry style.
What the design should include:
Bold headline: “WE’RE HIRING”
Sub-headline: “Leading Hand Boilermaker & Dragline Fitter”
Key points:
• Tallon Basin based
• Dragline & shovel maintenance
• Great pay + long-term work
• Locally owned & operated
KPR logo placed cleanly
Space for 1–2 images (boilermaking or dragline work)
Design style:
Strong and industrial
Blue/white colour scheme
Easy to read at a glance
Suitable for a square 1080×1080 design

```html
<!DOCTYPE html>
<html lang="en">
<head>
<meta charset="UTF-8">
<title>KPR Site Services – We're Hiring</title>
<link href="https://fonts.googleapis.com/css2?family=Playfair+Display:wght@900&family=Poppins:wght@400;600;700&display=swap" rel="stylesheet">
<style>
  :root {
    --stage: #dcfbfb;
    --navy: #0c1633;
    --navy-deep: #0a1028;
    --royal: #1a4ff0;
    --sky: #4fc9ee;
    --cyan: #5ed8f6;
    --white: #ffffff;
    --silver-light: #f4f6f8;
    --silver-dark: #9aa3ab;
  }
  * { margin: 0; padding: 0; box-sizing: border-box; }
  html, body {
    width: 1200px; height: 720px; overflow: hidden;
    background: var(--stage);
    font-family: "Poppins", sans-serif;
  }
  .post {
    position: absolute; left: 268px; top: 28px;
    width: 664px; height: 664px; overflow: hidden;
    box-shadow: 0 6px 18px rgba(0, 40, 50, 0.35);
    background: var(--navy);
  }
  .post__photo {
    position: absolute; inset: 0;
    background:
      radial-gradient(ellipse 70% 45% at 22% 88%, rgba(225, 220, 190, 0.75), rgba(225, 220, 190, 0) 70%),
      linear-gradient(180deg, rgba(0,0,0,0) 45%, rgba(80, 200, 225, 0.55) 62%, rgba(40, 110, 160, 0.4) 100%),
      linear-gradient(115deg, #1d63f2 0%, #1a46e0 30%, #14308f 55%, #0d1a45 75%, var(--navy-deep) 100%);
  }
  .post__shade {
    position: absolute; inset: 0;
    background: linear-gradient(100deg, rgba(10,16,40,0) 40%, rgba(10,16,40,0.55) 62%, rgba(10,16,40,0.85) 100%);
  }
  .brand {
    position: absolute; left: 30px; top: 82px;
    display: flex; align-items: center; gap: 10px;
    color: var(--white); font-weight: 700; font-size: 24px;
    letter-spacing: 0.5px;
  }
  .brand__dot {
    width: 22px; height: 22px; border-radius: 50%;
    background: var(--cyan);
  }
  .headline {
    position: absolute; right: 52px; top: 14px;
    text-align: right; font-family: "Playfair Display", serif; font-weight: 900;
    line-height: 0.95;
  }
  .headline__top {
    display: block; font-size: 104px; letter-spacing: -3px;
    background: linear-gradient(180deg, var(--silver-light) 0%, var(--silver-dark) 55%, var(--silver-light) 100%);
    -webkit-background-clip: text; background-clip: text; color: transparent;
  }
  .headline__bottom {
    display: block; font-size: 98px; color: var(--cyan); letter-spacing: -2px;
    margin-top: -4px;
  }
  .roles {
    position: absolute; right: 54px; top: 210px;
    text-align: right; color: var(--white);
    font-weight: 700; font-size: 31px; line-height: 1.16;
  }
  .perks { position: absolute; right: 52px; top: 306px; list-style: none; }
  .perk {
    position: absolute; right: 0; height: 18px;
    background: var(--sky);
    clip-path: polygon(8px 0, 100% 0, 100% 100%, 0 100%);
    color: var(--white); font-size: 14.5px; line-height: 18px;
    padding: 0 6px 0 14px; white-space: nowrap;
    display: flex; align-items: center; gap: 4px;
  }
  .perk svg { width: 11px; height: 11px; }
  .photos { position: absolute; left: 272px; top: 476px; width: 344px; height: 90px; }
  .photos__item {
    position: absolute; top: 0; height: 90px; width: 180px;
    clip-path: polygon(30px 0, 100% 0, calc(100% - 30px) 100%, 0 100%);
    background: var(--cyan);
  }
  .photos__item span {
    position: absolute; inset: 2px;
    clip-path: polygon(29px 0, 100% 0, calc(100% - 29px) 100%, 0 100%);
  }
  .photos__item--weld { left: 0; }
  .photos__item--weld span { background: radial-gradient(circle at 55% 45%, #8aa0ff 0%, #26307a 30%, #0f1640 80%); }
  .photos__item--grind { left: 162px; }
  .photos__item--grind span { background: radial-gradient(circle at 45% 55%, #b46a2a 0%, #3a2c26 40%, #15151a 85%); }
  .contact {
    position: absolute; right: 54px; top: 596px; text-align: right; color: var(--white);
  }
  .contact__phone {
    display: flex; justify-content: flex-end; align-items: center; gap: 8px;
    color: var(--cyan); font-weight: 700; font-size: 28px; line-height: 1;
  }
  .contact__web {
    display: flex; justify-content: flex-end; align-items: center; gap: 8px;
    font-size: 15px; margin-top: 4px;
  }
</style>
</head>
<body>
  <main class="post">
    <div class="post__photo" role="img" aria-label="Photo of a worker's hard hat overlooking a coastal mine site and conveyor"></div>
    <div class="post__shade"></div>

    <div class="brand"><span class="brand__dot"></span>KPR Site Services</div>

    <h1 class="headline">
      <span class="headline__top">WE’RE</span>
      <span class="headline__bottom">HIRING</span>
    </h1>

    <h2 class="roles">Leading Hand Boilermaker<br>&amp; Dragline Fitter</h2>

    <ul class="perks">
      <li class="perk" style="top:0">Tallon Basin based
        <svg viewBox="0 0 12 12"><circle cx="6" cy="6" r="5" fill="none" stroke="#fff" stroke-width="1.2"/><path d="M3.5 6.2l1.8 1.7 3.3-3.6" fill="none" stroke="#fff" stroke-width="1.2"/></svg></li>
      <li class="perk" style="top:41px">Dragline &amp; shovel maintenance
        <svg viewBox="0 0 12 12"><circle cx="6" cy="6" r="5" fill="none" stroke="#fff" stroke-width="1.2"/><path d="M3.5 6.2l1.8 1.7 3.3-3.6" fill="none" stroke="#fff" stroke-width="1.2"/></svg></li>
      <li class="perk" style="top:82px">Great pay + long-term work
        <svg viewBox="0 0 12 12"><circle cx="6" cy="6" r="5" fill="none" stroke="#fff" stroke-width="1.2"/><path d="M3.5 6.2l1.8 1.7 3.3-3.6" fill="none" stroke="#fff" stroke-width="1.2"/></svg></li>
      <li class="perk" style="top:123px">Locally owned &amp; operated
        <svg viewBox="0 0 12 12"><circle cx="6" cy="6" r="5" fill="none" stroke="#fff" stroke-width="1.2"/><path d="M3.5 6.2l1.8 1.7 3.3-3.6" fill="none" stroke="#fff" stroke-width="1.2"/></svg></li>
    </ul>

    <div class="photos">
      <div class="photos__item photos__item--weld"><span role="img" aria-label="Photo of a boilermaker welding"></span></div>
      <div class="photos__item photos__item--grind"><span role="img" aria-label="Photo of a fitter grinding on dragline equipment"></span></div>
    </div>

    <div class="contact">
      <div class="contact__phone">0400 555 018
        <svg width="12" height="22" viewBox="0 0 12 22"><rect x="1" y="1" width="10" height="20" rx="2" fill="none" stroke="#fff" stroke-width="1.5"/><line x1="4" y1="18" x2="8" y2="18" stroke="#fff" stroke-width="1.2"/></svg>
      </div>
      <div class="contact__web">www.kprsiteservices.com
        <svg width="14" height="14" viewBox="0 0 14 14"><circle cx="7" cy="7" r="6" fill="#fff"/><path d="M1 7h12M7 1c-3 3-3 9 0 12M7 1c3 3 3 9 0 12" fill="none" stroke="#0c1633" stroke-width="0.9"/></svg>
      </div>
    </div>
  </main>
</body>
</html>
```